Letterhead Design for Law Firm

**Edit: I have added the photo of a bottom that I like.

------
We are looking for a re-design of our new letterhead. The letterhead is for a law firm and will be used for digital and traditionally printed correspondence.

Here are some suggestions:

- Please use colours are #8ec900 and simple black.
- Please do not use any type of "waves" at the bottom of the page. This is not in style at all.
- Please stay modern yet conservative.
- Please use font Segoe UI Light or similar if you can
- Avoid clipart or illustrations.
- Utilize ample white space in the layout so the design looks clean and information is easy to read at a glance. Don't overcrowd the letterhead.
- Make sure the letterhead design is consistent with our brand identity (see corvelith.ca)
-Please, no black headers or footers.

I am attaching my current letterhead and signature for your convenience.

Remember, the letterhead is an extension of our professional identity. We are a successful firm and trial lawyers who correspond with insurers, judges, lawyers, courts, clients, etc. Make it new, modern, attractive, yet powerful and conservative.

It needs to be easily printable. I would like the bleed removed in print so the black bar the bottom crosses the page (but the text is not near the edges)
Updates

Low design quality

Target Market(s)

Clients, Government Offices, Judiciary, Lawyers, Insurance Companies, Colleagues.

Industry/Entity Type

Law

Other font styles liked:
• Segoe UI LIght, Calibri Light,

Colors
00AB8E
00BBA5
67D7C9
C6EFE9
E9F9F6

Requirements
Must have
• Everything that is on the letterhead now.
Nice to have
• Cutting Edge design, yet conservative.
Should not have
• law firm cliche design, images,

```html
<!DOCTYPE html>
<html lang="en">
<head>
<meta charset="utf-8">
<title>Marlowe Personal Injury Lawyers – Letterhead</title>
<link href="https://fonts.googleapis.com/css2?family=Roboto:wght@400;500&family=Arimo&display=swap" rel="stylesheet">
<style>
  :root {
    --backdrop: #3b3b3b;
    --paper: #f6f4f5;
    --ink: #1c1c1c;
    --text: #333333;
    --muted: #555555;
    --accent: #8ec900;
    --bar: #1a1a1a;
    --rule: #3a3a3a;
  }
  * { box-sizing: border-box; margin: 0; padding: 0; }
  html, body { width: 935px; height: 1200px; overflow: hidden; background: var(--backdrop); }
  .letterhead {
    position: absolute; left: 40px; top: 0; width: 854px; height: 1200px;
    background: var(--paper); overflow: hidden;
    font-family: "Roboto", sans-serif; color: var(--ink);
    box-shadow: 0 0 18px rgba(0,0,0,.45);
  }
  .abs { position: absolute; }
  .firm-name { left: 40px; top: 62px; width: 254px; text-align: center; font-weight: 400; }
  .firm-name .name-main { display: block; font-size: 58px; line-height: 66px; letter-spacing: 0.5px; }
  .firm-name .name-sub { display: block; font-size: 14px; letter-spacing: 1.6px; margin-top: 2px; white-space: nowrap; }
  .practice { right: 276px; top: 56px; text-align: right; font-size: 13.8px; line-height: 18.8px; color: var(--text); }
  .practice strong { font-weight: 500; color: var(--ink); }
  .divider { left: 596px; top: 44px; width: 1px; height: 147px; background: #8a8a8a; }
  .contact { left: 617px; top: 49px; font-size: 13.8px; line-height: 18.8px; color: var(--text); white-space: nowrap; }
  .contact-row { display: flex; align-items: center; gap: 7px; }
  .contact-row svg { width: 12px; height: 12px; flex: none; }
  .file-clerk { margin-top: 9px; }
  .file-clerk strong { font-weight: 500; color: var(--ink); }
  .file-clerk span { color: var(--muted); }
  .label { font-size: 15px; font-weight: 500; }
  .without-prejudice { left: 40px; top: 197px; }
  .by-email { left: 39px; top: 245px; }
  .date { right: 43px; top: 245px; font-size: 15px; }
  .recipient { left: 40px; top: 292px; font-size: 16px; line-height: 19.9px; font-style: normal; }
  .attention { left: 40px; top: 425px; font-size: 16px; }
  .salutation { left: 40px; top: 452px; font-size: 16px; }
  .re-label { left: 40px; top: 488px; font-size: 15px; font-weight: 500; }
  .re-lines { left: 292px; top: 487px; font-size: 16px; line-height: 19.9px; }
  .subject-rule { left: 51px; top: 568px; width: 745px; height: 1px; background: var(--rule); }
  .body-text { left: 50px; top: 607px; width: 759px; font-family: "Arimo", sans-serif; font-size: 13.7px; line-height: 20.4px; color: var(--text); text-align: justify; hyphens: auto; }
  .body-text p + p { margin-top: 20.4px; }
  .closing { left: 51px; top: 920px; font-size: 14px; line-height: 17.7px; }
  .signature { left: 53px; top: 973px; width: 232px; height: 50px; background: linear-gradient(90deg, #dcdadb, #ecebeb); border-radius: 3px; }
  .signatory { left: 55px; top: 1043px; font-size: 14px; line-height: 17.7px; }
  .footer-line { left: 0; top: 1169px; width: 854px; height: 4px; background: var(--bar); }
  .footer-bar { left: 0; top: 1178px; width: 854px; height: 22px; background: var(--bar); }
</style>
</head>
<body>
<main class="letterhead">
  <div class="abs firm-name"><span class="name-main">MARLOWE</span><span class="name-sub">PERSONAL INJURY LAWYERS</span></div>

  <div class="abs practice">
    <strong>Practice Restricted</strong><br>
    Serious Personal Injury<br>
    Wrongful Death Litigation<br>
    Long-Term Disability Litigation<br>
    Wrongful Dismissal Litigation<br>
    Employee Terminations
  </div>
  <div class="abs divider"></div>
  <div class="abs contact">
    <div>40 Queen Street E., Suite 910</div>
    <div>Ashford, ON&nbsp; L3X 2B7</div>
    <div class="contact-row"><svg viewBox="0 0 16 16"><path fill="var(--accent)" d="M3.6 1.2l2.3 2.6c.4.4.3 1-.1 1.4L4.6 6.3c.9 2 2.6 3.8 4.9 4.9l1.1-1.2c.4-.4 1-.5 1.4-.1l2.6 2.3c.4.4.4 1 0 1.4l-1.3 1.3C10.6 16.2 0 5.6 1.1 2.9L2.2 1.2c.4-.4 1-.4 1.4 0z"/></svg>905-555-0142</div>
    <div class="contact-row"><svg viewBox="0 0 16 16"><rect x="4" y="1" width="8" height="5" fill="var(--accent)"/><rect x="1" y="6" width="14" height="6" rx="1" fill="var(--accent)"/><rect x="4" y="10" width="8" height="5" fill="var(--accent)" stroke="var(--paper)" stroke-width="1"/></svg>905-555-0178</div>
    <div class="contact-row"><svg viewBox="0 0 16 16"><rect x="1" y="3" width="14" height="10" fill="var(--accent)"/><path d="M1.5 3.5L8 9l6.5-5.5" fill="none" stroke="var(--paper)" stroke-width="1.3"/></svg>Email: carla@corvelith.ca</div>
    <div class="contact-row"><svg viewBox="0 0 16 16"><circle cx="8" cy="8" r="7" fill="var(--accent)"/><path d="M4 5c2 0 2 2 3 3s-1 3 0 4M10 3c-1 2 1 3 3 3M9 10c1 0 2 1 2 3" fill="none" stroke="var(--paper)" stroke-width="1.2"/></svg>www.CORVELITH.ca</div>
    <div class="file-clerk"><strong>File Clerk:</strong> <span>Carla Dunmore</span></div>
  </div>

  <div class="abs label without-prejudice">Without Prejudice</div>
  <div class="abs label by-email">By Email</div>
  <div class="abs date">March 13, 2024</div>

  <address class="abs recipient">
    Brightmere Insurance Company<br>
    Claims Litigation Department<br>
    220 Fernhill Road North<br>
    P.O. Box 3100<br>
    Milbrook, ON&nbsp;&nbsp; N4K 2T6
  </address>

  <div class="abs attention">Attention:&nbsp; Mr. Nolan Reyes</div>
  <div class="abs salutation">Mr. Reyes:</div>

  <div class="abs re-label">Re:</div>
  <div class="abs re-lines">
    Harwick v. Delmonte et al.<br>
    DOL:&nbsp; September 12, 2019<br>
    Pre-Mediation Settlement Proposal – March 13th, 2024
  </div>
  <div class="abs subject-rule"></div>

  <div class="abs body-text">
    <p>Lorem ipsum dolor sit amet, consectetur adipiscing elit. Donec orci purus, luctus vitae dignissim eu, iaculis sed purus. Vivamus faucibus, ipsum nec aliquet viverra, leo mauris condimentum ligula, sit amet sagittis enim ligula quis arcu. Nam egestas tortor ivisi porttitor mattis. In tortor ante, ultricies in suscipit a, tempus non massa. Vivamus et auctor mi. Fusce vel massa nulla. Phasellus nec eros mauris, et scelerisque orci.</p>
    <p>Donec malesuada orci vitae nulla accumsan porta a id massa. Quisque accumsan iaculis magna sit amet fringilla. Maecenas consequat, magna eget tincidunt semper, odio nibh rutrum mi, id feugiat ante nisi eu risus. Vestibulum nunc orci, rhoncus a placerat in, ultricies in mi. Cras mattis varius eros, vel fringilla nisi suscipit eget. Quisque scelerisque sagittis nulla at porttitor.</p>
    <p>Sed id augue vitae urna euismod commodo aliquet a quam. Pellentesque arcu velit, cursus et malesuada ut, consequat et diam. Nullam erat sem, rhoncus id ullamcorper vitae, rhoncus et arcu. In ultricies ultricies nulla, ut rutrum nisi iaculis</p>
  </div>

  <div class="abs closing">Yours very truly,<br>MARLOWE PERSONAL INJURY LAWYERS</div>
  <div class="abs signature" role="img" aria-label="Handwritten signature of the signing lawyer"></div>
  <div class="abs signatory">
    Owen T. Marlowe<br>
    Marlowe Law Professional Corporation<br>
    /cd<br>
    Encl.
  </div>

  <div class="abs footer-line"></div>
  <div class="abs footer-bar"></div>
</main>
</body>
</html>
```